KorvaNest - Home Income and Business Resources Platform

I am looking for a website template for a multi-purposed website. This website will feature:

1.) Website Directory with Ratings & comments on listings
2.) Company Blog
3.) Homepage with Content (see files for homepage mock)

I would like the Design to have a default width 1170px (wider then normal)

Of course I am looking for Pages for Listings to be designed.

Great looking BLOG Layout: http://journal.plimworks.example/html/blog.html

I would like 4 Versions of a Website Directory Listing "Box"
1.) Basic Listing Box
2.) Sponsored Listing Box
3.) Recommended Listing Box
4.) Stay Away From Listing Box

Information on the Listing Page (Like on a Category Page)
Site Name, Site URL, Website Image, # of Views, Rating and # of Comments

Information on the Listing Details Page:
Same as ABOVE + About website Description, Vornic Score, Category Information

Decent looking examples is here: https://samples.trevolin.example/directory/computers/ and http://www.zqrankhub.example/.

I will include some sketches and screenshots of things I like/looking for. As designers,you have creative freedom and are encouraged to show this. This is Phase one of this project and winning designer is guaranteed to have future work for this project.

Target Market(s)

Directory, business, websites

Industry/Entity Type

Business

Coding

Coded - Design and coding required

Number of Pages Required

5+ page

Font styles to use
Sans Serif

Colors

Designer to choose colors to be used in the design.

Requirements
Must have
• Professional yet clean look. The use of Icons & images
• Unique Look
Should not have
• Any exact copies of any examples I provided

```html
<!DOCTYPE html>
<html lang="en">
<head>
<meta charset="utf-8">
<title>KorvaNest – Home</title>
<link href="https://fonts.googleapis.com/css2?family=Open+Sans:wght@400;600;700&display=swap" rel="stylesheet">
<style>
:root{
  --brand:#1a72bd;
  --ink:#222;
  --body:#555;
  --panel:#f2f2f2;
  --rule:#ececec;
  --footer:#ededed;
  --white:#fff;
}
*{box-sizing:border-box;margin:0;padding:0}
html,body{width:1200px;height:853px;overflow:hidden;background:var(--white)}
body{font-family:"Open Sans",Arial,sans-serif;color:var(--ink);position:relative}
.site-header{position:absolute;left:132px;top:22px;width:936px;height:50px}
.brand-name{position:absolute;left:0;top:0;font-size:40px;font-weight:400;color:var(--brand);letter-spacing:.3px;line-height:50px}
.main-nav{position:absolute;right:0;top:19px;display:flex;gap:31px;font-size:13px}
.main-nav a{color:var(--ink);text-decoration:none}
.main-nav a.is-active{color:var(--brand)}
.about-panel{position:absolute;left:132px;top:110px;width:720px;height:200px;background:var(--panel);padding:24px 24px 0 24px}
.about-panel h1{font-size:22px;font-weight:400;color:var(--brand);line-height:28px;margin-bottom:8px}
.about-panel p{font-size:10.4px;line-height:19.2px;color:var(--body);text-align:justify}
.sponsor{position:absolute;left:866px;width:200px;height:200px;overflow:hidden;color:var(--white)}
.sponsor--office{top:110px;background:linear-gradient(135deg,#c9782a 0%,#8a4a1a 45%,#2a2a32 100%)}
.sponsor--home{top:326px;background:linear-gradient(160deg,#5b6b8c 0%,#4a5878 55%,#3c4868 100%)}
.sponsor-label{position:absolute;left:10px;top:8px;font-size:11.5px;letter-spacing:.1px}
.sponsor-tag{position:absolute;left:60px;bottom:26px;line-height:1}
.sponsor-tag strong{display:block;font-size:14px;font-weight:600}
.sponsor-tag span{font-size:8.5px}
.sponsor--home .sponsor-tag{bottom:20px}
.feature{position:absolute;top:326px;width:228px}
.feature--income{left:132px}
.feature--ads{left:378px}
.feature--earn{left:624px}
.feature-photo{height:160px}
.photo-desk{background:linear-gradient(135deg,#e9e1d6 0%,#8a6a4e 50%,#2b2420 100%)}
.photo-tablet{background:linear-gradient(135deg,#f2f2f2 0%,#e6ebf0 45%,#4b78b8 100%)}
.photo-coins{background:linear-gradient(180deg,#f4f9fb 0%,#cfe5f4 45%,#2a6fc4 80%,#6aa6e0 100%)}
.feature-head{display:flex;align-items:flex-start;gap:12px;margin-top:20px;height:58px;border-bottom:3px solid var(--rule)}
.feature-head svg{flex:none;margin-top:3px}
.feature-head h2{font-size:18.5px;font-weight:400;color:var(--brand);line-height:22.5px}
.feature p{margin-top:14px;font-size:10.4px;line-height:17.6px;color:var(--body);text-align:justify}
.site-footer{position:absolute;left:0;top:797px;width:1200px;height:56px;background:var(--footer)}
.copyright{position:absolute;left:131px;top:19px;font-size:12px;color:var(--ink)}
.social{position:absolute;left:1009px;top:15px;display:flex;gap:6px}
.social span{width:26px;height:26px;border-radius:50%;display:block}
.social .s1{background:#3b5a9a}
.social .s2{background:#2aa3e0}
</style>
</head>
<body>
<header class="site-header">
  <div class="brand-name">KorvaNest</div>
  <nav class="main-nav">
    <a href="#" class="is-active">Home</a>
    <a href="#">About Us</a>
    <a href="#">Services</a>
    <a href="#">Contact Us</a>
  </nav>
</header>

<section class="about-panel">
  <h1>About KorvaNest</h1>
  <p>Aenean sed quam non sapien faucibus consequat vitae sit amet orci. Praesent quis risus mi. In mollis nulla in pulvinar dictum. Vivamus interdum sagittis felis, ut dapibus ligula feugiat ac. In dictum sapien eu tellus finibus fermentum. Aenean faucibus lacus ut mollis commodo. Donec vestibulum odio sem, ac laoreet massa ullamcorper id. Donec molestie nisi et tellus hendrerit vehicula. Nunc eu ligula sed quam pulvinar maximus in vitae eros. Proin porta fermentum ipsum, vel porttitor turpis venenatis luctus. Vivamus volutpat eu sapien quis tempus. Aenean feugiat viverra lorem ac sagittis. Donec sit amet lectus nec mi tempor laoreet ac nec nunc. Duis id auctor sapien. Curabitur ac elit leo. In eleifend dui tellus, in scelerisque elit porttitor et. Integer eu massa lacinia, lacinia nulla non, volutpat purus.</p>
</section>

<aside class="sponsor sponsor--office" role="img" aria-label="Sponsored listing photo: businessman seated in an orange armchair">
  <div class="sponsor-label">SPONSORED LISTINGS</div>
  <div class="sponsor-tag"><strong>TEXT HERE</strong><span>Sub text here</span></div>
</aside>
<aside class="sponsor sponsor--home" role="img" aria-label="Sponsored listing photo: hand holding a small model house">
  <div class="sponsor-label">SPONSORED LISTINGS</div>
  <div class="sponsor-tag"><strong>TEXT HERE</strong><span>Sub text here</span></div>
</aside>

<article class="feature feature--income">
  <div class="feature-photo photo-desk" role="img" aria-label="Photo: person writing in a notebook at a wooden desk"></div>
  <div class="feature-head">
    <svg width="31" height="36" viewBox="0 0 31 36" fill="none" stroke="var(--brand)" stroke-width="2.4"><path d="M2 2h18l9 9v23H2z"/><path d="M20 2v9h9"/><path d="M8 17h15M8 22h15M8 27h15"/></svg>
    <h2>Home Income<br>Resource Directory</h2>
  </div>
  <p>Find what you need, when you need it.The KorvaNest website directory is your one-stop pit for anything involved in making money from home, marketing your business or finding a new opportunity. Our modern, community supported directory will help you keep upto todate with the lastest information in a sensible fashion</p>
</article>

<article class="feature feature--ads">
  <div class="feature-photo photo-tablet" role="img" aria-label="Photo: man in blue shirt using a tablet with envelope icons"></div>
  <div class="feature-head">
    <svg width="36" height="34" viewBox="0 0 36 34" fill="var(--brand)"><path d="M2 11h8l16-9v26L10 19H2z"/><path d="M6 20h6l3 11H9z"/><rect x="29" y="12" width="5" height="6" rx="1"/></svg>
    <h2>Advertising<br>Benefits</h2>
  </div>
  <p>Everyone needs to advertise and we know just how to get your offer out to the right people. We have many methods including: Text ads, E-mail, Display, newsletter and even some old school methods available to make your next campaign a success. Advertise a website, a link text, full page circular or a small display ad and get results. Every advertiser recieves a dedicated account manager that will handle everything for You.</p>
</article>

<article class="feature feature--earn">
  <div class="feature-photo photo-coins" role="img" aria-label="Photo: stacks of coins in blue light"></div>
  <div class="feature-head">
    <svg width="38" height="28" viewBox="0 0 38 28"><rect x="1.5" y="3.5" width="35" height="21" fill="none" stroke="var(--brand)" stroke-width="3"/><rect x="6" y="8" width="26" height="12" fill="var(--brand)"/><circle cx="19" cy="14" r="6" fill="var(--white)"/><path d="M18 11h2v6h-2z" fill="var(--brand)"/></svg>
    <h2>Earning With<br>KorvaNest</h2>
  </div>
  <p>Join KorvaNest and start earning money. When you share KorvaNest and lock in an advertiser or premium listing, we reward you. Build a downline at any of our listed sites when you share KorvaNest with NO extra work. Its all done for you.We also offer a revenue share program for true supporters of our mission.</p>
</article>

<footer class="site-footer">
  <div class="copyright">Copyright &copy; 2017 KorvaNest.&nbsp;&nbsp; All rights reserved.</div>
  <div class="social"><span class="s1" aria-label="Social link"></span><span class="s2" aria-label="Social link"></span></div>
</footer>
</body>
</html>
```